Transform Your Giving

I need a tri-fold brochure that will fit in a standard number 10 business envelope. Meadowlark and Allied Services is a charitable nonprofit. The goal of this brochure is to stimulate people into thinking about other ways to make a donation. The design should communicate the essential information on donation options, create a sense of professional integrity, be graphically sharp, easy to read and laid out in a way that doesn't make the material appear crowded.

```html
<!DOCTYPE html>
<html lang="en">
<head>
<meta charset="utf-8">
<title>Transform Your Giving – Tri-fold Brochure</title>
<link href="https://fonts.googleapis.com/css2?family=Montserrat:ital,wght@0,300;0,400;0,500;0,600;0,700;0,800;0,900;1,400&display=swap" rel="stylesheet">
<style>
:root{
  --navy:#2b2470;
  --green:#4cb748;
  --white:#ffffff;
  --paper:#efeef1;
  --stage:#9a9899;
  --ink:#2e2b4a;
}
*{box-sizing:border-box;margin:0;padding:0}
html,body{width:1200px;height:1200px;overflow:hidden;background:var(--stage);font-family:'Montserrat',sans-serif;color:var(--ink)}
.spread{position:absolute;left:277px;width:648px;height:504px;overflow:hidden}
.spread.outside{top:88px}
.spread.inside{top:632px;background:var(--paper)}
.panel{position:absolute;top:0;width:216px;height:504px;overflow:hidden}
.abs{position:absolute}
.ctr{text-align:center}

/* outside: impact panel */
.impact{left:0;background:var(--white)}
.impact-title{top:20px;left:0;width:216px;font-weight:900;font-size:15.5px;line-height:19px;color:var(--navy)}
.impact-title span{color:var(--green)}
.impact-text{top:63px;left:20px;width:176px;font-size:7.6px;line-height:9.6px;font-weight:400}
.checklist{top:135px;left:43px;width:130px;list-style:none}
.checklist li{height:16px;margin-bottom:5px;border:1px solid var(--green);font-size:8.4px;line-height:14px;text-align:center}
.checklist li svg{vertical-align:-1px;margin-right:3px}

/* outside: contact panel */
.contact{left:213px;width:214px;background:var(--green);color:var(--white)}
.wordmark{font-weight:800;letter-spacing:1px}
.contact .wordmark{top:24px;left:0;width:214px;font-size:28px;line-height:30px}
.contact .tagline{top:60px;left:0;width:214px;font-size:4.6px;font-weight:700;letter-spacing:.3px}
.contact-intro{top:88px;left:20px;width:174px;font-size:8.9px;line-height:10.9px;font-weight:500}
.quote{top:187px;left:33px;width:155px;height:47px;border:1px solid var(--white);border-radius:8px;padding:8px 10px 0;font-size:6.6px;line-height:9px}
.quote em{font-weight:400}
.quote b{display:block;margin-top:3px;font-weight:700}
.quote-mark{top:176px;left:0;width:214px;font-size:26px;font-weight:900;line-height:20px}
.will{top:241px;left:0;width:214px;font-size:7.8px;line-height:11px}
.will .url{font-size:12px;font-weight:800;line-height:14px}
.will .small{font-weight:300}
.will b{font-weight:800;font-size:8.8px}
.pill-navy{top:310px;left:60px;width:96px;height:16px;background:var(--navy);border-radius:9px;font-size:10px;font-weight:800;line-height:16px;color:var(--white)}
.questions{top:333px;left:0;width:214px;font-size:7.8px;line-height:9.8px;font-weight:400}
.questions b{font-size:10.6px;font-weight:800;display:block;line-height:13px}
.info{left:56px;width:150px;font-size:6.2px;line-height:8px;font-weight:400}
.info b{font-weight:700}
.info-ico{left:56px}
.info-text{left:79px;font-size:6.4px;line-height:8px}
.follow{top:445px;left:0;width:214px;font-size:7.8px}
.follow i{display:inline-block;width:11px;height:11px;border-radius:50%;background:var(--navy);vertical-align:-2px;margin-left:4px}
.disclaimer{top:469px;left:24px;width:168px;font-size:3.4px;line-height:4.4px}

/* outside: cover panel */
.cover{left:425px;width:223px;background:var(--navy)}
.cover-head{top:212px;left:0;width:223px;color:var(--white)}
.cover-head .lead{font-size:11.6px;font-weight:400}
.be{font-size:21px;font-weight:900;color:var(--white);line-height:30px}
.be span{color:var(--green)}
.be svg{vertical-align:-3px;margin-right:3px}
.cover-sub{top:292px;left:0;width:223px;color:var(--white);font-size:7.4px;line-height:9.4px;font-style:italic}
.ways{top:338px;left:12px;width:206px;height:60px}
.way{position:absolute;width:40px;text-align:center;font-size:5.4px;font-weight:700;color:var(--white);line-height:7px}
.way .ring{width:34px;height:34px;margin:0 auto 3px;border:1.5px solid var(--green);border-radius:50%;display:flex;align-items:center;justify-content:center}
.cover .wordmark{top:436px;left:0;width:223px;font-size:34px;color:var(--navy);line-height:36px}
.cover .tagline{top:474px;left:0;width:223px;font-size:5.6px;font-weight:800;color:var(--navy);letter-spacing:.3px}

/* inside */
.ways-badge{top:18px;left:17px;width:163px;height:57px;background:var(--navy);border-radius:29px 29px 29px 0;color:var(--white)}
.ways-badge .num{position:absolute;left:16px;top:2px;font-size:50px;font-weight:900;color:var(--green);line-height:54px}
.ways-badge .txt{position:absolute;left:49px;top:7px;font-size:13.6px;font-weight:900;line-height:13.5px}
.icon-disc{position:absolute;width:54px;height:54px;border-radius:50%;background:var(--navy);display:flex;align-items:center;justify-content:center}
.way-title{position:absolute;font-size:11px;line-height:13.4px;font-weight:700;color:var(--navy)}
.way-lead{position:absolute;font-size:6.6px;line-height:8.6px;font-weight:700;color:var(--green)}
.copy{position:absolute;font-size:7.5px;line-height:9.6px;font-weight:400;color:var(--ink)}
.copy.small{font-size:7px;line-height:8.7px}
.how{position:absolute;height:13px;padding:0 6px;background:var(--green);color:var(--white);font-size:7.6px;line-height:13px;font-weight:500;border-radius:0 6px 6px 6px}
.ticks{list-style:none}
.ticks li{position:relative;padding-left:15px;margin-bottom:5px}
.ticks li svg{position:absolute;left:0;top:1px}
.col-rule{position:absolute;top:0;width:1px;height:504px;background:#dcdbe0}
</style>
</head>
<body>

<!-- Outside spread -->
<section class="spread outside">

  <article class="panel impact">
    <h2 class="abs impact-title ctr">THE IMPACT OF<br><span>YOUR GIFT</span></h2>
    <p class="abs impact-text ctr">Your generosity drives our mission. With every Strategic and Smart gift, your generosity reaches further and drives our mission. Join our community and begin your Strategic and Smart Giving with us today.</p>
    <ul class="abs checklist">
      <li><svg width="8" height="8" viewBox="0 0 10 10"><circle cx="5" cy="5" r="4.2" fill="none" stroke="#4cb748" stroke-width="1.1"/><path d="M3 5.2l1.5 1.4L7.2 3.6" fill="none" stroke="#4cb748" stroke-width="1.1"/></svg>Stocks and Securities</li>
      <li><svg width="8" height="8" viewBox="0 0 10 10"><circle cx="5" cy="5" r="4.2" fill="none" stroke="#4cb748" stroke-width="1.1"/><path d="M3 5.2l1.5 1.4L7.2 3.6" fill="none" stroke="#4cb748" stroke-width="1.1"/></svg>DAFs</li>
      <li><svg width="8" height="8" viewBox="0 0 10 10"><circle cx="5" cy="5" r="4.2" fill="none" stroke="#4cb748" stroke-width="1.1"/><path d="M3 5.2l1.5 1.4L7.2 3.6" fill="none" stroke="#4cb748" stroke-width="1.1"/></svg>QCDs</li>
      <li><svg width="8" height="8" viewBox="0 0 10 10"><circle cx="5" cy="5" r="4.2" fill="none" stroke="#4cb748" stroke-width="1.1"/><path d="M3 5.2l1.5 1.4L7.2 3.6" fill="none" stroke="#4cb748" stroke-width="1.1"/></svg>Crypto</li>
      <li><svg width="8" height="8" viewBox="0 0 10 10"><circle cx="5" cy="5" r="4.2" fill="none" stroke="#4cb748" stroke-width="1.1"/><path d="M3 5.2l1.5 1.4L7.2 3.6" fill="none" stroke="#4cb748" stroke-width="1.1"/></svg>Charitable Annuity</li>
    </ul>
    <svg class="abs" style="left:0;top:290px" width="216" height="214" viewBox="0 0 216 214">
      <defs>
        <linearGradient id="coupleTone" x1="0" y1="0" x2="1" y2="1">
          <stop offset="0" stop-color="#e9a447"/>
          <stop offset=".45" stop-color="#8a5a3c"/>
          <stop offset="1" stop-color="#5a2e28"/>
        </linearGradient>
      </defs>
      <path d="M0 30 Q108 -20 216 30 L216 214 L0 214Z" fill="#4cb748"/>
      <path d="M0 38 Q108 -6 216 38 L216 214 L0 214Z" fill="#ffffff"/>
      <path d="M0 44 Q108 2 216 44 L216 214 L0 214Z" fill="url(#coupleTone)" role="img" aria-label="Photo of a smiling senior couple hiking outdoors at sunset, holding a map"/>
    </svg>
  </article>

  <article class="panel contact">
    <div class="abs wordmark ctr">MAAS</div>
    <div class="abs tagline ctr">MEADOWLARK AND ALLIED SERVICES, INC.</div>
    <p class="abs contact-intro ctr">To learn more about Smart Giving Options and how they can benefit you and Meadowlark and Allied Services, please reach out to our team. We're here to help you navigate these giving methods and answer any question you may have.</p>
    <div class="abs quote-mark ctr">&ldquo;</div>
    <blockquote class="abs quote ctr"><em>Being kind to others is a way of being good to yourself.</em><b>Helen Ashford</b></blockquote>
    <div class="abs will ctr">If you do not have a will<br><span class="url">go to www.OpenWillNow.org</span><br><span class="small">In 20 minutes you can have a</span><br><b>legal will – for free.</b></div>
    <div class="abs pill-navy ctr">CONTACT US</div>
    <div class="abs questions ctr"><b>Have more questions?</b>Please contact us at Meadowlark and<br>Allied Services</div>

    <svg class="abs info-ico" style="top:372px" width="18" height="18" viewBox="0 0 18 18"><circle cx="9" cy="9" r="8.3" fill="none" stroke="#fff" stroke-width=".8"/><path d="M9 4.2a3 3 0 0 0-3 3c0 2.2 3 6 3 6s3-3.8 3-6a3 3 0 0 0-3-3z" fill="none" stroke="#fff" stroke-width=".8"/><circle cx="9" cy="7.2" r="1" fill="#fff"/></svg>
    <div class="abs info-text" style="top:374px">2207 Kestrel Ave., Suite 4<br>Riverton, ND&nbsp; 58510</div>
    <svg class="abs info-ico" style="top:396px" width="18" height="18" viewBox="0 0 18 18"><circle cx="9" cy="9" r="8.3" fill="none" stroke="#fff" stroke-width=".8"/><rect x="6.4" y="4.5" width="5.2" height="9" rx="1" fill="none" stroke="#fff" stroke-width=".8"/></svg>
    <div class="abs info-text" style="top:397px">Call us Today!<br><b>701-555-0142</b> (ext. 100)</div>
    <svg class="abs info-ico" style="top:417px" width="18" height="18" viewBox="0 0 18 18"><circle cx="9" cy="9" r="8.3" fill="none" stroke="#fff" stroke-width=".8"/><circle cx="9" cy="9" r="4.2" fill="none" stroke="#fff" stroke-width=".7"/><path d="M4.8 9h8.4M9 4.8c-2 2.4-2 6 0 8.4M9 4.8c2 2.4 2 6 0 8.4" fill="none" stroke="#fff" stroke-width=".6"/></svg>
    <div class="abs info-text" style="top:418px">dmorgan@meadowlarkallied.org<br><b>www.meadowlarkallied.org</b></div>

    <div class="abs follow ctr">Follow us <i></i></div>
    <p class="abs disclaimer ctr">This brochure is shared for general information only and does not offer tax, legal or accounting advice. Meadowlark and Allied Services is not a financial adviser. Please speak with your own tax or financial professional before you choose any Smart Giving option.</p>
  </article>

  <article class="panel cover">
    <svg class="abs" style="left:0;top:0" width="223" height="200" viewBox="0 0 223 200">
      <defs>
        <linearGradient id="farmTone" x1="0" y1="0" x2="0" y2="1">
          <stop offset="0" stop-color="#9fb37a"/>
          <stop offset=".5" stop-color="#5f7f3a"/>
          <stop offset="1" stop-color="#3f5a2a"/>
        </linearGradient>
      </defs>
      <path d="M0 0H223V168 Q130 200 0 168Z" fill="#4cb748"/>
      <path d="M0 0H223V160 Q130 190 0 160Z" fill="url(#farmTone)" role="img" aria-label="Photo of a smiling young farmer in a cap and denim shirt leaning on a tool in a green field"/>
    </svg>
    <div class="abs cover-head ctr">
      <div class="lead">Transform Your Giving</div>
      <div class="be"><svg width="18" height="18" viewBox="0 0 20 20"><circle cx="10" cy="10" r="8.5" fill="none" stroke="#4cb748" stroke-width="2"/><path d="M6 10.5l3 3 6-7" fill="none" stroke="#4cb748" stroke-width="2.2"/></svg>Be <span>Strategic</span></div>
      <div style="height:1px;background:#fff;width:180px;margin:0 auto"></div>
      <div class="be"><svg width="18" height="18" viewBox="0 0 20 20"><circle cx="10" cy="10" r="8.5" fill="none" stroke="#4cb748" stroke-width="2"/><path d="M6 10.5l3 3 6-7" fill="none" stroke="#4cb748" stroke-width="2.2"/></svg>Be <span>Smart</span></div>
      <div style="height:1px;background:#fff;width:146px;margin:0 auto"></div>
    </div>
    <p class="abs cover-sub ctr">Discover the impact of Smart Giving with<br>Meadowlark and Allied Services</p>
    <div class="abs ways">
      <div class="way" style="left:0;top:8px"><div class="ring"><svg width="18" height="18" viewBox="0 0 20 20"><circle cx="10" cy="10" r="8" fill="none" stroke="#fff" stroke-width="1.1"/><text x="10" y="14" font-size="10" font-weight="700" fill="#fff" text-anchor="middle" font-family="Montserrat,sans-serif">B</text></svg></div>Crypto</div>
      <div class="way" style="left:40px;top:-2px"><div class="ring"><svg width="18" height="18" viewBox="0 0 20 20" fill="none" stroke="#fff" stroke-width="1.1"><path d="M2 7L10 3l8 4z"/><path d="M4 8v7M8 8v7M12 8v7M16 8v7M2 16h16"/></svg></div>DAF's</div>
      <div class="way" style="left:80px;top:-8px"><div class="ring"><svg width="18" height="18" viewBox="0 0 20 20" fill="none" stroke="#fff" stroke-width="1.1"><path d="M3 17V11h3v6M8.5 17V8h3v9M14 17V5h3v12M2 17h16M3 8l5-3 4 2 5-4"/></svg></div>Stocks<br>&amp; Securities</div>
      <div class="way" style="left:120px;top:-2px"><div class="ring"><svg width="18" height="18" viewBox="0 0 20 20" fill="none" stroke="#fff" stroke-width="1.1"><rect x="3" y="8" width="14" height="9"/><rect x="2" y="5.5" width="16" height="3"/><path d="M10 5.5V17M10 5.5c-2-3-5-2-3 0M10 5.5c2-3 5-2 3 0"/></svg></div>QCDs</div>
      <div class="way" style="left:160px;top:8px"><div class="ring"><svg width="18" height="18" viewBox="0 0 20 20" fill="none" stroke="#fff" stroke-width="1.1"><circle cx="8.5" cy="10.5" r="6"/><path d="M8.5 6.5v4l2.5 1.5M7 3h3"/><circle cx="15" cy="14" r="3.2"/></svg></div>Charitable<br>Annuity</div>
    </div>
    <svg class="abs" style="left:0;top:405px" width="223" height="99" viewBox="0 0 223 99">
      <path d="M0 30 Q111 -12 223 30 V99 H0Z" fill="#4cb748"/>
      <path d="M0 38 Q111 -2 223 38 V99 H0Z" fill="#ffffff"/>
    </svg>
    <div class="abs wordmark ctr">MAAS</div>
    <div class="abs tagline ctr">MEADOWLARK AND ALLIED SERVICES, INC.</div>
  </article>
</section>

<!-- Inside spread -->
<section class="spread inside">
  <div class="col-rule" style="left:213px"></div>
  <div class="col-rule" style="left:427px"></div>

  <svg class="abs" style="left:90px;top:0" width="470" height="118" viewBox="0 0 470 118">
    <defs>
      <linearGradient id="driveTone" x1="0" y1="0" x2="1" y2="0">
        <stop offset="0" stop-color="#7c8d5a"/>
        <stop offset=".45" stop-color="#9cb8d2"/>
        <stop offset="1" stop-color="#3e5f8f"/>
      </linearGradient>
    </defs>
    <path d="M0 0H470 Q420 40 380 70 Q250 130 120 70 Q60 40 0 0Z" fill="#4cb748"/>
    <path d="M0 0H470 Q420 34 380 60 Q250 116 120 60 Q60 34 0 0Z" fill="url(#driveTone)" role="img" aria-label="Photo of a cheerful senior man driving a blue convertible along a country road"/>
  </svg>

  <div class="abs ways-badge"><span class="num">5</span><span class="txt">STRATEGIC<br>AND SMART<br>WAYS TO GIVE</span></div>

  <!-- Column 1 -->
  <div class="icon-disc" style="left:17px;top:87px"><svg width="30" height="30" viewBox="0 0 20 20" fill="none" stroke="#fff" stroke-width=".9"><path d="M3 17V11h3v6M8.5 17V8h3v9M14 17V5h3v12M2 17h16M3 8l5-3 4 2 5-4"/></svg></div>
  <h3 class="way-title" style="left:80px;top:89px">Gifts of Stocks or<br>Appreciated Assets<br>Strategic &amp; Smart</h3>
  <p class="way-lead" style="left:80px;top:134px;width:125px">Consider your long-term publicly traded stock as a way to give to your favorite charity.</p>
  <p class="copy" style="left:18px;top:164px;width:190px">You can make a significantly bigger impact when you donate long-term appreciated securities, including stock, mutual funds, and bonds, directly to your favorite charity.</p>
  <div class="how" style="left:18px;top:207px">How Does It Work?</div>
  <p class="copy" style="left:18px;top:224px;width:190px">When you donate stock to a charity, you will generally take a tax deduction for the full market value. Because you are donating stock, your contribution and tax deduction may be significantly higher than contributing the after-tax proceeds. The same benefits apply when you donate mutual funds or bonds.</p>

  <div class="icon-disc" style="left:17px;top:300px"><svg width="28" height="28" viewBox="0 0 20 20" fill="none" stroke="#fff" stroke-width=".9"><path d="M2 7L10 3l8 4z"/><path d="M4 8v7M8 8v7M12 8v7M16 8v7M2 16h16"/></svg></div>
  <h3 class="way-title" style="left:80px;top:304px">Donor-Advised<br>Fund (DAF)<br>Strategic &amp; Smart</h3>
  <p class="way-lead" style="left:79px;top:351px;width:128px">Consider a DAF – a simple, flexible, and tax-advantageous way to give to your favorite charities.</p>
  <p class="copy" style="left:18px;top:382px;width:190px">A Donor-Advised Fund (DAF), is like a charitable investment account for the sole purpose of supporting your favorite charities.</p>
  <div class="how" style="left:18px;top:413px">How Does It Work?</div>
  <p class="copy small" style="left:18px;top:431px;width:190px">You establish a DAF and contribute cash, stocks, or non-publicly traded assets, cryptocurrency, and private company stock to be eligible for an immediate tax deduction. Those funds are contributed for tax-free growth. You can recommend grants be made from your DAF to any IRS qualified public charity.</p>

  <!-- Column 2 -->
  <div class="icon-disc" style="left:235px;top:148px"><svg width="30" height="30" viewBox="0 0 20 20"><circle cx="10" cy="10" r="8" fill="none" stroke="#fff" stroke-width=".9"/><circle cx="10" cy="10" r="6" fill="none" stroke="#fff" stroke-width=".6"/><text x="10" y="13.6" font-size="9.5" font-weight="700" fill="#fff" text-anchor="middle" font-family="Montserrat,sans-serif">B</text></svg></div>
  <h3 class="way-title" style="left:299px;top:151px">Cryptocurrency<br>Strategic &amp; Smart</h3>
  <p class="way-lead" style="left:299px;top:183px;width:115px">Consider donating Bitcoin and other cryptocurrencies to your favorite charity.</p>
  <p class="copy" style="left:235px;top:213px;width:186px">Bitcoin and other cryptocurrencies can be donated to charity just like other appreciated assets such as stocks and other business interests. Before you sell bitcoin and donate the after-tax proceeds, consider donating your bitcoin directly to a favorite charity.</p>
  <div class="how" style="left:235px;top:274px">How Does It Work?</div>
  <div class="copy" style="left:235px;top:294px;width:188px">
    <p style="margin-bottom:5px">Many donors find it useful to open a Donor-Advised Fund (DAF). This strategy includes two significant benefits, both for you and your favorite charity.</p>
    <ul class="ticks">
      <li><svg width="10" height="10" viewBox="0 0 10 10"><circle cx="5" cy="5" r="4.2" fill="none" stroke="#4cb748" stroke-width="1"/><path d="M3 5.2l1.5 1.4L7.2 3.6" fill="none" stroke="#4cb748" stroke-width="1"/></svg>Your tax deduction will be equal to the fair market value of the donated bitcoin (as determined by a qualified appraisal).</li>
      <li><svg width="10" height="10" viewBox="0 0 10 10"><circle cx="5" cy="5" r="4.2" fill="none" stroke="#4cb748" stroke-width="1"/><path d="M3 5.2l1.5 1.4L7.2 3.6" fill="none" stroke="#4cb748" stroke-width="1"/></svg>Your cryptocurrency donation is tax-smart because it may eliminate capital gains taxes on the value / appreciation AND your favorite charity will receive 100% of the value of the contribution.</li>
    </ul>
    <p style="margin-top:4px">Often charities are not able to accept direct donations of bitcoin/crypto so using a DAF is a great way to donate these assets.</p>
  </div>
  <svg class="abs" style="left:213px;top:470px" width="214" height="34" viewBox="0 0 214 34">
    <path d="M0 34 Q107 -12 214 34Z" fill="#4cb748"/>
    <path d="M0 34 Q107 0 214 34Z" fill="#2b2470"/>
  </svg>

  <!-- Column 3 -->
  <div class="icon-disc" style="left:440px;top:43px"><svg width="28" height="28" viewBox="0 0 20 20" fill="none" stroke="#fff" stroke-width=".9"><rect x="3" y="8" width="14" height="9"/><rect x="2" y="5.5" width="16" height="3"/><path d="M10 5.5V17M10 5.5c-2-3-5-2-3 0M10 5.5c2-3 5-2 3 0"/></svg></div>
  <h3 class="way-title" style="left:506px;top:41px">Qualified Charitable<br>Distributions (QCDs)<br>Strategic &amp; Smart</h3>
  <p class="way-lead" style="left:506px;top:85px;width:125px">Consider a QCD – when planning your IRA withdrawal strategy...and donate to your favorite charity.</p>
  <p class="copy" style="left:441px;top:115px;width:200px">IRA owners at age 70 ½ or over can transfer dollars from their IRA to charity tax-free each year. These transfers known as Qualified Charitable Distributions (QCDs) offer eligible older Americans a great way to easily give to charity.</p>
  <div class="how" style="left:441px;top:167px">How Does It Work?</div>
  <p class="copy" style="left:441px;top:185px;width:202px">Are you 72 and required to take a minimum distribution (RMD) from your IRA but do not need the funds? Consider a Qualified Charitable Distribution. Normally, distributions from a traditional IRA are taxable when received. With a QCD, these distributions become tax-free when paid directly from the IRA to your favorite eligible charity. An IRA owner wishing to make a QCD should contact their IRA trustee, allowing time to complete the transaction before the end of the year to receive the tax benefit.</p>

  <div class="icon-disc" style="left:440px;top:295px"><svg width="30" height="30" viewBox="0 0 20 20" fill="none" stroke="#fff" stroke-width=".9"><circle cx="8.5" cy="10.5" r="6"/><path d="M8.5 6.5v4l2.5 1.5M7 3h3"/><circle cx="15" cy="14" r="3.2"/></svg></div>
  <h3 class="way-title" style="left:511px;top:294px">Charitable Gift<br>Annuity<br>Strategic &amp; Smart</h3>
  <p class="way-lead" style="left:511px;top:339px;width:120px">Consider establishing a Charitable Gift Annuity</p>
  <p class="copy" style="left:440px;top:361px;width:200px">You make a donation to a single charity. The gift is set aside in a reserve account and invested.</p>
  <div class="how" style="left:440px;top:384px">How Does It Work?</div>
  <p class="copy" style="left:440px;top:402px;width:202px">A charitable gift annuity is a contract between a donor and a charity. As a donor, you make a sizable gift to a charity. using cash, securities, or possibly other assets. This money is then invested. In return, you become eligible to take a partial tax deduction for your donation, plus you receive a fixed stream of income from the charity for the rest of your life. At the end of your life (as well as your spouse's, if you're giving as a couple), the charity receives the remainder of the gift.</p>
</section>

</body>
</html>
```